Health Clinic treating people with mental illness needs a website

We need a website for a new mental health clinic based in Florida called Solvane Wellness USA. We treat people with mental health issues such as depression, PTSD, Bipolar, chronic pain, etc. I want the website to be easy to follow and inviting to the visitors. It should be easy to locate the different treatment options and how to go about contacting and making appointments. The images on the website should be something that the patients can relate to, whether a close up of a woman's face, something that conveys emotion. The patients visiting this website are often sad and miserable, they need to be able to feel comfortable when they look at this website. I want them to feel that we understand where they are coming from. I like colors such as purple, turquoise, lavender.

Target Market(s)

College students, veterans, anyone with mental illness

Industry/Entity Type

Health And Wellness

Font styles to use
Serif
Sans Serif

Colors

Designer to choose colors to be used in the design.

Requirements
Must have
• There should be a home/landing page, about us page, treatment page, contact page, and a FAQ page. I've included my logo below.
Nice to have
• The flow of the web pages should be calming and welcoming. I want people to feel warm and understood when they enter our page.
Should not have
• The images and writing should not be overly stimulating or aggressive.

```html
<!DOCTYPE html>
<html lang="en">
<head>
<meta charset="utf-8">
<title>Solvane Wellness USA</title>
<link href="https://fonts.googleapis.com/css2?family=IBM+Plex+Sans:wght@400;500;600;700&family=Open+Sans:wght@400;600&display=swap" rel="stylesheet">
<style>
:root{
  --purple:#7b2382;
  --purple-deep:#5e1a66;
  --teal:#2aa98b;
  --ink:#2b2b2b;
  --text:#444;
  --blush:#f5f1f2;
  --white:#fff;
  --line:#d6d6d6;
}
*{margin:0;padding:0;box-sizing:border-box}
html,body{width:1200px;height:4409px;overflow:hidden}
body{position:relative;background:var(--white);font-family:"Open Sans",sans-serif;color:var(--text)}
.abs{position:absolute}
h2{font-family:"IBM Plex Sans",sans-serif;font-weight:700;color:var(--ink);letter-spacing:.5px}
.section-title{position:absolute;left:0;width:1200px;text-align:center;font-size:25px}
.btn{position:absolute;background:var(--teal);color:#fff;font-family:"IBM Plex Sans",sans-serif;font-weight:600;display:flex;align-items:center;justify-content:center;letter-spacing:.5px}

/* header */
.brand{left:0;width:1200px;top:40px;text-align:center;font-family:"IBM Plex Sans",sans-serif;font-weight:600;font-size:30px;color:var(--purple)}
.brand .dot{display:inline-block;width:14px;height:14px;border-radius:50%;background:var(--teal);margin-left:8px;vertical-align:middle}
.nav{top:114px;left:365px;display:flex;gap:37px;font-family:"IBM Plex Sans",sans-serif;font-weight:600;font-size:14px;color:var(--ink)}
.nav .active{color:var(--purple);text-decoration:underline;text-underline-offset:4px}
.social{top:109px;left:974px;display:flex;gap:9px}
.social span{width:26px;height:26px;border-radius:50%;background:var(--purple-deep)}
.social span:first-child{background:#2f4fa0}
.social span:nth-child(2){background:#2a9be0}

/* hero */
.hero{top:157px;left:0;width:1200px;height:531px;background:linear-gradient(180deg,#d8cfb8 0%,#c9b27a 45%,#b58a35 80%,#8a6523 100%)}
.hero-title{top:275px;left:778px;font-family:"IBM Plex Sans",sans-serif;font-weight:700;color:var(--purple);line-height:1.05}
.hero-title .s{font-size:42px;display:block}
.hero-title .l{font-size:62px;display:block}

/* about */
.about{top:688px;left:0;width:1200px;height:575px;background:var(--blush)}
.about-photo{top:50px;left:74px;width:544px;height:477px;background:linear-gradient(135deg,#e8e2da,#a8b7c8 50%,#c98a7a)}
.about h2{position:absolute;top:100px;left:666px;font-size:37px}
.about p{position:absolute;left:669px;width:385px;font-size:14.5px;line-height:22px}

/* why */
.why-band{top:1409px;left:0;width:1200px;height:526px;background:linear-gradient(180deg,#6a6057 0%,#3f3a36 50%,#2d2824 100%)}
.why-card{top:1455px;left:149px;width:902px;height:423px;background:#fff}
.feature{position:absolute;width:240px;text-align:center}
.feature svg{display:block;margin:0 auto 12px}
.feature h3{font-family:"IBM Plex Sans",sans-serif;font-weight:600;font-size:13px;color:var(--ink);margin-bottom:6px}
.feature p{font-size:12.5px;line-height:17px}

/* treatment */
.treat{top:1935px;left:0;width:1200px;height:927px;background:var(--blush)}
.card{position:absolute;background:#fff;box-shadow:0 2px 8px rgba(0,0,0,.08)}
.card .ph{width:100%}
.card .lbl{font-family:"IBM Plex Sans",sans-serif;font-weight:700;font-size:16px;color:var(--ink);padding:18px 0 0 26px;letter-spacing:.4px}

/* faq */
.faq-item{position:absolute;left:293px;width:601px;height:43px;border:1px solid var(--line);display:flex;align-items:center;padding-left:24px;font-size:14.5px;color:var(--ink)}
.faq-item .tog{position:absolute;right:6px;top:10px;width:24px;height:23px;background:var(--teal);color:#fff;font-size:16px;display:flex;align-items:center;justify-content:center}
.faq-item .tog.open{background:#a3489f}
.faq-answer{top:3058px;left:293px;width:570px;font-size:12.5px;line-height:17px}

/* articles */
.articles{top:3347px;left:0;width:1200px;height:549px;background:var(--blush)}
.article .title{font-family:"IBM Plex Sans",sans-serif;font-weight:700;font-size:16.5px;color:var(--ink);padding:22px 26px 8px}
.article p{font-size:13px;line-height:19px;padding:0 26px}

/* contact */
.contact-panel{top:3896px;left:0;width:599px;height:439px;background:linear-gradient(135deg,#8e2f93,#7a2080)}
.contact-panel h2{position:absolute;top:100px;left:145px;font-size:27px;color:#fff}
.contact-panel p{position:absolute;left:145px;font-size:12.5px;line-height:23px;color:#f1e2f2}
.field{position:absolute;border-bottom:1px solid #999;font-size:13px;color:var(--ink);padding-bottom:10px}
.submit{position:absolute;top:4173px;left:656px;width:393px;height:44px;background:var(--purple);color:#fff;font-family:"IBM Plex Sans",sans-serif;font-weight:700;font-size:17px;display:flex;align-items:center;justify-content:center}
.footer{top:4335px;left:0;width:1200px;height:74px;background:var(--blush);display:flex;align-items:center;justify-content:center;font-size:11px;color:var(--ink)}
</style>
</head>
<body>

<header>
  <div class="abs brand">Solvane Wellness USA<span class="dot"></span></div>
  <nav class="abs nav">
    <span class="active">HOME</span><span>ABOUT US</span><span>TREATMENT</span><span>FAQ</span><span>CONTACT US</span>
  </nav>
  <div class="abs social"><span></span><span></span><span></span></div>
</header>

<section>
  <div class="abs hero" role="img" aria-label="Smiling woman with open arms in a golden field at sunset"></div>
  <h1 class="abs hero-title"><span class="s">WELCOME TO</span><span class="l">SOLVANE</span><span class="l">WELLNESS</span></h1>
  <div class="btn" style="top:487px;left:786px;width:271px;height:62px;font-size:19px">BOOK AN APPOINTMENT</div>
</section>

<section class="abs about">
  <div class="abs about-photo" role="img" aria-label="Thoughtful woman talking with a counsellor in a bright room"></div>
  <h2>ABOUT US</h2>
  <p style="top:172px">Lorem ipsum dolor sit amet, consectetur adipiscing elit, sed do eiusmod tempor incididunt ut labore et dolore magna aliqua. Ut enim ad minim veniam, quis nostrud exercitation ullamco laboris nisi ut aliquip ex ea commodo consequat. Duis aute irure dolor in reprehenderit in voluptate.</p>
  <p style="top:339px">Duis aute irure dolor in reprehenderit in voluptate velit esse cillum dolore eu fugiat nulla pariatur error sit voluptatem accusantium doloremque laudantium, totam rem aperiam, eaque ipsa quae ab illo inventore veritatis</p>
</section>

<h2 class="section-title" style="top:1313px">WHY CHOOSE US</h2>
<div class="abs" style="top:1353px;left:0;width:1200px;text-align:center;font-size:14.5px">Lorem ipsum dolor</div>

<div class="abs why-band" role="img" aria-label="Person raising arms on a hillside at dusk"></div>
<div class="abs why-card">
  <div class="feature" style="left:36px;top:38px">
    <svg width="52" height="50" viewBox="0 0 52 50"><path d="M8 30a18 18 0 0 1 36 0" fill="none" stroke="#7b2382" stroke-width="5"/><rect x="4" y="28" width="11" height="18" rx="4" fill="#7b2382"/><rect x="37" y="28" width="11" height="18" rx="4" fill="#7b2382"/></svg>
    <h3>SUPPORT</h3><p>Duis aute irure dolor in repreh enderit in voluptate velit esse cillum dolore eu fugiat nulla pariatur.</p></div>
  <div class="feature" style="left:331px;top:38px">
    <svg width="52" height="50" viewBox="0 0 52 50"><rect x="4" y="22" width="10" height="24" fill="#7b2382"/><path d="M17 24l8-18c4 0 6 3 5 7l-2 7h16c3 0 4 3 3 5l-4 18c-1 2-2 3-4 3H17z" fill="#7b2382"/></svg>
    <h3>SATISFACTION</h3><p>Duis aute irure dolor in repreh enderit in voluptate velit esse cillum dolore eu fugiat nulla pariatur.</p></div>
  <div class="feature" style="left:621px;top:38px">
    <svg width="52" height="50" viewBox="0 0 52 50"><circle cx="26" cy="9" r="6" fill="#7b2382"/><path d="M26 18v30M26 30l-14-12M26 30l14-12" stroke="#7b2382" stroke-width="5" fill="none" stroke-linecap="round"/></svg>
    <h3>BETTER HEALTH</h3><p>Duis aute irure dolor in repreh enderit in voluptate velit esse cillum dolore eu fugiat nulla pariatur.</p></div>
  <div class="feature" style="left:36px;top:227px">
    <svg width="52" height="50" viewBox="0 0 52 50"><circle cx="26" cy="25" r="22" fill="#7b2382"/><path d="M16 25l7 7 13-14" stroke="#fff" stroke-width="4.5" fill="none" stroke-linecap="round" stroke-linejoin="round"/></svg>
    <h3>LOREM IPSUM</h3><p>Duis aute irure dolor in repreh enderit in voluptate velit esse cillum dolore eu fugiat nulla pariatur.</p></div>
  <div class="feature" style="left:331px;top:227px">
    <svg width="52" height="50" viewBox="0 0 52 50"><path d="M26 30C14 20 16 8 26 14c10-6 12 6 0 16z" fill="#7b2382"/><path d="M4 26l10 18h24l10-18" fill="none" stroke="#7b2382" stroke-width="5" stroke-linejoin="round"/></svg>
    <h3>LOREM IPSUM</h3><p>Duis aute irure dolor in repreh enderit in voluptate velit esse cillum dolore eu fugiat nulla pariatur.</p></div>
  <div class="feature" style="left:621px;top:227px">
    <svg width="52" height="50" viewBox="0 0 52 50"><rect x="6" y="8" width="34" height="38" fill="none" stroke="#7b2382" stroke-width="4"/><path d="M20 34l4-10 18-18 6 6-18 18z" fill="#7b2382"/></svg>
    <h3>LOREM IPSUM</h3><p>Duis aute irure dolor in repreh enderit in voluptate velit esse cillum dolore eu fugiat nulla pariatur.</p></div>
</div>

<section class="abs treat"></section>
<h2 class="section-title" style="top:1988px">OUR TREATMENT</h2>
<div class="card" style="top:2070px;left:137px;width:298px;height:316px"><div class="ph" style="height:245px;background:linear-gradient(135deg,#6a574c,#3a2e29)" role="img" aria-label="Woman sitting alone on a sofa, looking down"></div><div class="lbl">DEPRESSION</div></div>
<div class="card" style="top:2070px;left:452px;width:296px;height:316px"><div class="ph" style="height:245px;background:linear-gradient(135deg,#5b5b5b,#1c1c1c)" role="img" aria-label="Black and white portrait of a distressed woman"></div><div class="lbl">PTSD</div></div>
<div class="card" style="top:2070px;left:765px;width:296px;height:316px"><div class="ph" style="height:245px;background:linear-gradient(180deg,#b9cbe0,#8fa5c0 70%,#5a3e2a)" role="img" aria-label="Man sitting against a wall holding his head"></div><div class="lbl">BIPOLAR</div></div>
<div class="card" style="top:2407px;left:137px;width:298px;height:315px"><div class="ph" style="height:245px;background:linear-gradient(135deg,#3e5257,#8a6c60 60%,#c9553b)" role="img" aria-label="Person holding a painful elbow"></div><div class="lbl">CHRONIC PAIN</div></div>
<div class="card" style="top:2407px;left:452px;width:296px;height:315px"><div class="ph" style="height:245px;background:linear-gradient(180deg,#2f2f2f,#6a5a4a 60%,#bbb)" role="img" aria-label="Young woman sitting cross-legged with head in hands"></div><div class="lbl">MINDFULNESS</div></div>
<div class="card" style="top:2407px;left:765px;width:296px;height:315px"><div class="ph" style="height:245px;background:linear-gradient(135deg,#e8e8e4,#b8aea4 60%,#2a2a2a)" role="img" aria-label="Worried woman resting her head on her hand"></div><div class="lbl">ANXIETY</div></div>
<div class="btn" style="top:2766px;left:488px;width:224px;height:46px;font-size:15px">BOOK AN APPOINTMENT</div>

<h2 class="section-title" style="top:2918px">FREQUENTLY ASKED QUESTIONS</h2>
<div class="faq-item" style="top:2998px">Lorem ipsum dolor sit amet consectetur adipiscing elit?<span class="tog open">−</span></div>
<p class="abs faq-answer">Sed ut perspiciatis unde omnis iste natus error sit voluptatem accusantdoloremque laudantium, totam rem aper eaque ipsa quae ab illo inventore veritatis easi architecto beatae vitae dicta sunt explicabo ipsam voluptatem.</p>
<div class="faq-item" style="top:3136px">Lorem ipsum dolor sit amet consectetur adipiscing elit?<span class="tog">+</span></div>
<div class="faq-item" style="top:3194px">Lorem ipsum dolor sit amet consectetur adipiscing elit?<span class="tog">+</span></div>
<div class="faq-item" style="top:3251px">Lorem ipsum dolor sit amet consectetur adipiscing elit?<span class="tog">+</span></div>

<section class="abs articles"></section>
<h2 class="section-title" style="top:3394px">LATEST ARTICLES</h2>
<article class="card article" style="top:3468px;left:132px;width:298px;height:367px"><div class="ph" style="height:245px;background:linear-gradient(135deg,#3a2a2a,#1a1a1a 60%,#7a2a30)" role="img" aria-label="Man holding his head in distress"></div><div class="title">LOREM IPSUM IS SIMPLY</div><p>Sed ut perspiciatis unde omnis iste natus error sit voluptatem.</p></article>
<article class="card article" style="top:3468px;left:452px;width:296px;height:367px"><div class="ph" style="height:245px;background:linear-gradient(180deg,#dcd6c8,#8a6a48 50%,#2f6a4a)" role="img" aria-label="Sad young woman sitting at a table"></div><div class="title">LOREM IPSUM IS SIMPLY</div><p>Sed ut perspiciatis unde omnis iste natus error sit voluptatem.</p></article>
<article class="card article" style="top:3468px;left:770px;width:298px;height:367px"><div class="ph" style="height:245px;background:linear-gradient(180deg,#c9c9c7,#9a9a98 70%,#2a2a2a)" role="img" aria-label="Woman sitting on the floor hugging her knees"></div><div class="title">LOREM IPSUM IS SIMPLY</div><p>Sed ut perspiciatis unde omnis iste natus error sit voluptatem.</p></article>

<section>
  <div class="abs contact-panel" role="img" aria-label="Purple-toned photo of a counselling conversation">
    <h2>GET IN TOUCH</h2>
    <p style="top:155px">I'm a paragraph. Click here to add your<br>own text and edit me.</p>
    <p style="top:220px">Address: 214 Harbor Palm Avenue<br>Sarasota, FL 34236</p>
    <p style="top:280px">Email: info@solvanewellness.com<br>Phone: 941-555-0142</p>
  </div>
  <div class="field" style="top:3996px;left:656px;width:178px">First Name</div>
  <div class="field" style="top:3996px;left:872px;width:178px">Last Name</div>
  <div class="field" style="top:4053px;left:656px;width:178px">Email</div>
  <div class="field" style="top:4053px;left:872px;width:178px">Subject</div>
  <div class="field" style="top:4109px;left:656px;width:394px">Type your message here...</div>
  <div class="submit">SUBMIT</div>
</section>

<footer class="abs footer">Copyright © 2019 All Rights Reserved</footer>
</body>
</html>
```